New Wine Label - Classy, Simple, Modern

We are a small boutique winery who have been making and selling wine for 21 years. We are called "Calloway Ridge Winery" and Calloway is the Greek God of wine. We have a classic label at the moment that we would like to modernise.

We are looking to update our labels while keeping some of the original elements.
From existing label to definitely keep:
1. Logo (Colour can be darkened to a very dark purple - almost black)
2. Legal requirements - Front Label: 750ml, variety, year, "Canberra District" Back Label: Produce of Australia, number of standard drinks, alc/vol, additives, internet address, bar code plus new requirement to warn pregnant women alcohol can harm their babies.
From existing label open to change:
3. What would be nice - Separate front and back labels. Focus on logo on front label (Possibly printed in a raised gloss/embossed), Modern Font,
4. What can we lose? Happy to lose the words about us.
5.Font - Modern, Colour - white background, Shape Rectangular Front approximately height 11cm width 9cm & Back height 9cm width 7cm.

Prototype label can be for a
Front:
2022 Cabernet Sauvignon, Canberra District, 750ml, Estate Grown and Made
Back
13.6%ALC/VOL, APPROX 8.0 STANDARD DRINKS, PRESERVATIVE (220) ADDED, PRODUCE OF AUSTRALIA, Bar Code, Pregnant women warning, www.calloway-ridge.com.au

if you want to use some words to describe the wine that's fine - you can make some up or use existing words from our website www.calloway-ridge.com.au

Files:
1 - Photo of existing front label
2 - Current printers spec sheet for front and back label
3 - Pregnancy warning graphic (specific details see link below - label type 1)
4 - Current Bar Code for Cabernet Sauvignon
Many file types of existing logo

Link to legal requirement for pregnant women warning - we need label type 1 -https://www.examplelabelrules.org/industry/labelling/Pages/pregnancy-warning-labels-downloadable-files.aspx

Target Market(s)
25 - 40 year olds, drink wine

Industry/Entity Type
Winery - Wine Production

```html
<!DOCTYPE html>
<html lang="en">
<head>
<meta charset="UTF-8">
<title>Calloway Ridge Winery – Cabernet Sauvignon Front Label</title>
<link rel="stylesheet" href="https://fonts.googleapis.com/css2?family=Cinzel:wght@400;500&family=Montserrat:wght@300;400&display=swap">
<style>
  :root {
    --page-bg: #f2f2f3;
    --label-bg: #ffffff;
    --label-border: #3a3a3a;
    --illustration-grey: #e4e4e4;
    --illustration-soft: #f4f4f4;
    --seal-gold: #f2c314;
    --ink: #1c1c1c;
    --variety-purple: #3b1e6e;
  }
  * { margin: 0; padding: 0; box-sizing: border-box; }
  html, body {
    width: 1200px;
    height: 1200px;
    overflow: hidden;
    background: var(--page-bg);
  }
  .front-label {
    position: absolute;
    left: 220px;
    top: 124px;
    width: 760px;
    height: 952px;
    background: var(--label-bg);
    border: 2px solid var(--label-border);
    overflow: hidden;
  }
  .label-illustration {
    position: absolute;
    left: 10px;
    top: 0;
    width: 750px;
    height: 952px;
    background:
      radial-gradient(ellipse 62% 48% at 62% 42%, var(--illustration-grey) 0%, var(--illustration-soft) 70%, rgba(255,255,255,0) 100%);
  }
  .label-line {
    position: absolute;
    left: 0;
    width: 100%;
    text-align: center;
    transform: translateY(-50%);
    white-space: nowrap;
  }
  .winery-seal {
    position: absolute;
    left: 323px;
    top: 83px;
    width: 116px;
    height: 116px;
    border-radius: 50%;
    background: var(--seal-gold);
  }
  .winery-name {
    top: 240px;
    font-family: 'Cinzel', serif;
    font-weight: 400;
    font-size: 26px;
    letter-spacing: 1.5px;
    color: var(--ink);
  }
  .region {
    top: 404px;
    font-family: 'Montserrat', sans-serif;
    font-weight: 400;
    font-size: 29px;
    letter-spacing: 8.5px;
    color: var(--ink);
  }
  .variety {
    top: 519px;
    font-family: 'Cinzel', serif;
    font-weight: 400;
    font-size: 62px;
    line-height: 50px;
    letter-spacing: 11px;
    color: var(--variety-purple);
  }
  .vintage {
    top: 719px;
    left: -15px;
    font-family: 'Montserrat', sans-serif;
    font-weight: 300;
    font-size: 78px;
    letter-spacing: 9px;
    color: var(--ink);
  }
  .volume {
    top: 917px;
    font-family: 'Montserrat', sans-serif;
    font-weight: 400;
    font-size: 33px;
    letter-spacing: 5px;
    color: var(--ink);
  }
</style>
</head>
<body>
  <main class="front-label">
    <div class="label-illustration" role="img" aria-label="Faint grey engraved illustration with vine leaves"></div>
    <div class="winery-seal" aria-hidden="true"></div>
    <p class="label-line winery-name">CALLOWAY RIDGE WINERY</p>
    <p class="label-line region">Canberra district</p>
    <h1 class="label-line variety">CABERNET<br>SAUVIGNON</h1>
    <p class="label-line vintage">2122</p>
    <p class="label-line volume">750ml</p>
  </main>
</body>
</html>
```